Re-Branding

I would like a new "brand" which will incorporate my new photo. I do title insurance in California for Harborline Deed Assurance Corp. Could be used on business cards or flyers.

Target Market(s)

Real Estate Professionals, Attorneys, Mortgage Companies and Banks.

Contact Information for Business Card

High Gloss

Requirements
Must have
• My photo, my logo and my contact information.
Nice to have
• background that is appealing to clients
Should not have
• home email address

```html
<!DOCTYPE html>
<html lang="en">
<head>
<meta charset="utf-8">
<title>Marisol Ortega – Account Executive</title>
<link rel="stylesheet" href="https://fonts.googleapis.com/css2?family=Libre+Bodoni:wght@400&family=Varela+Round&display=swap">
<style>
  :root {
    --brand-green: #08631f;
    --paper-top: #ffffff;
    --paper-bottom: #efefef;
    --ink-light: #ffffff;
    --ink-navy: #1b2657;
  }
  html, body {
    margin: 0;
    padding: 0;
    overflow: hidden;
  }
  .card {
    position: relative;
    width: 1200px;
    height: 771px;
    overflow: hidden;
    background: linear-gradient(180deg, var(--paper-top) 60%, var(--paper-bottom) 100%);
  }
  .card__band {
    position: absolute;
    inset: 0;
    width: 1200px;
    height: 771px;
  }
  .card__band polygon {
    fill: var(--brand-green);
  }
  .identity__name,
  .identity__title {
    position: absolute;
    left: 0;
    right: 0;
    margin: 0;
    text-align: center;
    color: var(--ink-light);
    line-height: 1;
  }
  .identity__name {
    top: 238px;
    font-family: "Libre Bodoni", "Bodoni Moda", serif;
    font-weight: 400;
    font-size: 94px;
    letter-spacing: -1px;
  }
  .identity__title {
    top: 336px;
    font-family: "Varela Round", sans-serif;
    font-size: 29px;
    letter-spacing: 1px;
    -webkit-text-stroke: 0.6px var(--ink-light);
  }
  .company {
    position: absolute;
    left: 0;
    right: 0;
    top: 668px;
    display: flex;
    justify-content: center;
    align-items: center;
    gap: 12px;
  }
  .company__dot {
    width: 38px;
    height: 38px;
    border-radius: 50%;
    background: var(--brand-green);
  }
  .company__name {
    font-family: "Libre Bodoni", "Bodoni Moda", serif;
    font-size: 28px;
    color: var(--ink-navy);
    line-height: 1;
  }
</style>
</head>
<body>
  <main class="card">
    <svg class="card__band" viewBox="0 0 1200 771" aria-hidden="true">
      <polygon points="0,0 1200,0 1200,556 139,624 0,534"/>
    </svg>

    <h1 class="identity__name">Marisol Ortega</h1>
    <p class="identity__title">account executive | vice president</p>

    <footer class="company">
      <span class="company__dot"></span>
      <span class="company__name">Harborline Deed Assurance Corp.</span>
    </footer>
  </main>
</body>
</html>
```